Business card for Eyelash extension salon in Beverly Hills,California USA

We need new business card for our salon in Beverly Hills. The salon name is 'Lashvera' . We would like to have...Business name: Lashvera Name of person: will provide later Address 4720 N.Alder Crest Ave Westmere Hills , CA 90299 Phone: will provide later (Text only) Web: www.lashverastudio.example Snapgrid icon, Circlebook icon follow us for seasonal campaign and news @lashverastudiolounge Design should look elegant, high-end, clean, simple, cohesive with my brand. Please refer my brand board. Business name color will be metallic bronzy color. Im thinking grey background or white background. Thanks

Target Market(s)

25-35. Gender neutral. People who are in Entertainment business industry.
This is High-end Eyelash extension salon in Beverly Hills

Industry/Entity Type

Beauty Salon

Contact Information for Business Card

Business name: Lashvera
Name of person: will provide later
Address 4720 N.Alder Crest Ave Westmere Hills , CA 90299
Phone: will provide later (Text only)
Web: www.lashverastudio.example
Snapgrid icon, Circlebook icon
follow us for seasonal campaign and news @lashverastudiolounge

Requirements
Must have
• Beautiful, elegant, clean and simple look but very attractive and modern
Should not have
• We don't like too clutter, too busy designs.

```html
<!DOCTYPE html>
<html lang="en">
<head>
<meta charset="utf-8">
<title>Lashvera Business Card</title>
<link rel="stylesheet" href="https://fonts.googleapis.com/css2?family=Work+Sans:wght@300;400;500;600&display=swap">
<style>
  :root {
    --backdrop: #2a2a2a;
    --bronze: #8a6a52;
    --bronze-light: #a27d62;
    --ink-black: #0c0c0c;
    --paper-white: #ffffff;
    --soft-white: rgba(255,255,255,0.85);
  }
  * { box-sizing: border-box; margin: 0; padding: 0; }
  html, body {
    width: 1200px; height: 800px; overflow: hidden;
    background: var(--backdrop);
    font-family: "Work Sans", sans-serif;
  }
  .canvas { position: relative; width: 1200px; height: 800px; }

  .card {
    position: absolute;
    width: 580px; height: 330px;
    border-radius: 22px;
    overflow: hidden;
    background: var(--bronze);
    box-shadow: 0 18px 40px rgba(0,0,0,0.45);
  }

  /* Front */
  .card-front { left: 90px; top: 70px; }
  .front-brand {
    position: absolute; right: 70px; top: 95px;
    font-size: 54px; font-weight: 300; letter-spacing: 2px;
    color: var(--paper-white);
  }
  .front-social {
    position: absolute; left: 44px; bottom: 38px;
    display: flex; align-items: center; gap: 14px;
    font-size: 13px; font-weight: 400; color: var(--paper-white);
  }
  .social-name { display: flex; align-items: center; gap: 6px; }
  .social-dot { width: 8px; height: 8px; border-radius: 50%; background: var(--paper-white); }

  /* Back */
  .card-back { left: 530px; top: 400px; display: flex; }
  .back-brand-strip {
    width: 180px; height: 100%;
    background: var(--ink-black);
    position: relative;
  }
  .strip-brand {
    position: absolute; left: 50%; top: 50%;
    transform: translate(-50%, -50%) rotate(90deg);
    font-size: 40px; font-weight: 300; letter-spacing: 2px;
    color: var(--bronze-light);
    white-space: nowrap;
  }
  .back-details {
    flex: 1; padding: 52px 40px 0 44px;
    color: var(--paper-white);
  }
  .person-name { font-size: 26px; font-weight: 600; letter-spacing: 0.5px; }
  .person-role { font-size: 15px; font-weight: 300; color: var(--soft-white); margin-top: 2px; }
  .contact-list { margin-top: 30px; font-size: 14px; line-height: 1.45; }
  .business-block { margin-top: 32px; font-size: 14px; line-height: 1.45; }
  .business-name { font-weight: 600; letter-spacing: 0.5px; margin-bottom: 4px; }
</style>
</head>
<body>
<main class="canvas">

  <section class="card card-front">
    <div class="front-brand">Lashvera</div>
    <div class="front-social">
      <span class="social-name"><span class="social-dot"></span>Snapgrid</span>
      <span class="social-name">Circlebook</span>
      <span class="social-handle">@lashverastudiolounge</span>
    </div>
  </section>

  <section class="card card-back">
    <div class="back-brand-strip">
      <div class="strip-brand">Lashvera</div>
    </div>
    <div class="back-details">
      <div class="person-name">Marlo Devane</div>
      <div class="person-role">Director</div>
      <div class="contact-list">
        <div>Mobile: 0410 555 017</div>
        <div>Email: marlo@lashverastudio.example</div>
      </div>
      <div class="business-block">
        <div class="business-name">LASHVERA</div>
        <div>4720 N.Alder Crest Ave</div>
        <div>Westmere Hills , CA 90299</div>
      </div>
    </div>
  </section>

</main>
</body>
</html>
```